Therapeutic Counselling Practice Brochure

I have a new therapeutic counselling practice in Melbourne.

I am making peri natal issues my special interest area.

I need a brochure targeted at new parents or pregnant women and partners, struggling with the concept of parenting, depression, maybe do not even know about it.

The feel should be safe and strong. I love the WREN website ( I do volunteer work with them)

Out of hours appointments and telephone counselling are important making my service very accessible.

Attached is an example for the content of the Brochure

Attached is an example for the content of the Brochure.

Target Market(s)

25 - 45 New Parents , expectant parents,families and friends of people struggling emotionally and mentally with and around being new parents

Requirements
Must have
• Feel of safety, somewhere to go for help, support, a conversation, soft ,strong
Nice to have
• mother and child, maybe parents and child, possibly a graphic, faceless

```html
<!DOCTYPE html>
<html lang="en">
<head>
<meta charset="utf-8">
<title>Maren Holloway – Perinatal Counselling Brochure</title>
<link href="https://fonts.googleapis.com/css2?family=Open+Sans:ital,wght@0,400;0,600;0,700;1,400;1,600&family=Ubuntu:wght@300;400;500;700&display=swap" rel="stylesheet">
<style>
  :root{
    --forest:#3d7a1e;
    --forest-deep:#2f6414;
    --leaf:#8cc63f;
    --lime:#b5d96a;
    --ink:#2b2b2b;
    --heading-green:#4a7d27;
    --soft-green:#7aa62e;
    --page:#ffffff;
    --stage:#efeee9;
    --panel-grey:#f3f3f1;
  }
  *{box-sizing:border-box;margin:0;padding:0}
  html,body{width:1200px;height:766px;overflow:hidden}
  body{background:var(--stage);position:relative;font-family:"Open Sans",Arial,sans-serif;color:var(--ink)}

  /* ---------- front cover ---------- */
  .cover{position:absolute;left:30px;top:33px;width:300px;height:700px;background:var(--page);overflow:hidden;box-shadow:0 2px 8px rgba(0,0,0,.18)}
  .cover-photo{position:absolute;left:0;top:100px;width:300px;height:340px;
    background:radial-gradient(circle at 72% 35%,#f7e6da 0,#f0cfb6 30%,#d9a587 62%,#b9826a 100%)}
  .cover-photo-fade{position:absolute;left:0;top:360px;width:300px;height:90px;background:linear-gradient(rgba(255,255,255,0),#fff)}
  .cover-shapes{position:absolute;left:0;top:0}
  .brand{position:absolute;left:22px;top:26px;display:flex;align-items:flex-start;gap:12px;color:#fff}
  .brand-dot{width:38px;height:38px;border-radius:50%;background:rgba(255,255,255,.85);margin-top:2px}
  .brand-name{font-family:"Open Sans",sans-serif;font-weight:700;font-size:21px;line-height:1.1}
  .brand-role{font-family:"Open Sans",sans-serif;font-weight:600;font-size:11.5px;margin-top:3px}
  .cover-headline{position:absolute;left:18px;top:452px;width:270px}
  .cover-headline h1{font-family:"Open Sans",sans-serif;font-weight:700;font-size:21px;line-height:1.2;color:var(--heading-green);letter-spacing:.2px}
  .cover-headline h2{font-family:"Open Sans",sans-serif;font-style:italic;font-weight:600;font-size:16.5px;color:var(--soft-green);margin-top:3px}
  .cover-intro{position:absolute;left:18px;top:548px;width:262px;font-style:italic;font-weight:600;font-size:11.2px;line-height:1.3;color:#2f5a14}

  /* ---------- inside spread ---------- */
  .spread{position:absolute;left:370px;top:33px;width:800px;height:700px;background:var(--page);overflow:hidden;box-shadow:0 2px 8px rgba(0,0,0,.18)}
  .panel{position:absolute;top:0;width:267px;height:700px;overflow:hidden}
  .panel-condition{left:0;background:var(--panel-grey)}
  .panel-impact{left:267px;background:#fff;border-left:1px solid #e2e2e2;border-right:1px solid #e2e2e2}
  .panel-selfcare{left:534px;width:266px;background:#fff}
  .band-top,.band-bottom{position:absolute;left:0}
  .band-bottom{top:628px}

  .photo-mother-baby{position:absolute;left:118px;top:40px;width:149px;height:210px;
    background:radial-gradient(ellipse at 60% 40%,#c9d0d2 0,#dfe4e5 45%,rgba(243,243,241,0) 75%)}
  .condition-title{position:absolute;left:24px;top:112px;font-family:"Ubuntu",sans-serif;font-weight:500;font-size:20px;line-height:1.25;color:var(--heading-green)}
  .condition-body{position:absolute;left:22px;top:232px;width:230px;font-size:10.2px;line-height:1.38}
  .condition-body p{margin-bottom:10px}
  .symptoms{list-style:none}
  .symptoms li{padding-left:9px;position:relative}
  .symptoms li::before{content:"•";position:absolute;left:0}

  .photo-sky{position:absolute;left:0;top:0;width:267px;height:250px;background:linear-gradient(#8fb7dc 0,#c6dcef 45%,#ffffff 100%)}
  .impact-body{position:absolute;left:20px;top:128px;width:228px;font-size:10.2px;line-height:1.38;text-align:justify}
  .impact-body p{margin-bottom:11px}
  .photo-consult{position:absolute;left:0;top:375px;width:267px;height:270px;
    background:linear-gradient(180deg,#fff 0,#eef2f4 18%,#dde6ea 55%,#cfd9de 100%)}

  .selfcare-title{position:absolute;left:18px;top:58px;font-family:"Ubuntu",sans-serif;font-weight:300;font-size:20px;color:var(--soft-green)}
  .selfcare-list{position:absolute;left:18px;top:104px;width:232px;font-size:9.8px;line-height:1.36}
  .selfcare-list h3{font-size:9.8px;font-weight:700;margin-top:10px}
  .selfcare-list h3:first-child{margin-top:0}
</style>
</head>
<body>

<section class="cover">
  <div class="cover-photo" role="img" aria-label="Photo of a mother cuddling her smiling baby"></div>
  <div class="cover-photo-fade"></div>
  <svg class="cover-shapes" width="300" height="700" viewBox="0 0 300 700" aria-hidden="true">
    <defs>
      <linearGradient id="coverFoot" x1="0" y1="0" x2="0" y2="1">
        <stop offset="0" stop-color="#ffffff" stop-opacity="0"/>
        <stop offset=".35" stop-color="#cfe5a4"/>
        <stop offset="1" stop-color="#8cc63f"/>
      </linearGradient>
    </defs>
    <path d="M0 0H300V105C210 110 110 160 0 310Z" fill="#b5d96a"/>
    <path d="M0 0H300V92C205 98 100 150 0 292Z" fill="#3d7a1e"/>
    <path d="M0 520C90 540 200 545 300 520V700H0Z" fill="url(#coverFoot)"/>
    <path d="M300 600C270 640 230 675 175 700H300Z" fill="#2f6414"/>
    <path d="M0 660C70 690 160 690 240 665C200 690 160 700 140 700H0Z" fill="#5f9b2b"/>
  </svg>
  <div class="brand">
    <span class="brand-dot"></span>
    <div>
      <div class="brand-name">Maren Holloway</div>
      <div class="brand-role">Counsellor and Personal Coach</div>
    </div>
  </div>
  <div class="cover-headline">
    <h1>ARE YOU EXPECTING<br>OR A NEW PARENT?</h1>
    <h2>Got the “Baby Blues”?</h2>
  </div>
  <p class="cover-intro">There is an expectation of happiness and fulfilment around childbirth.<br>Feeling “blue”, interferes with the adjustment to becoming a parent.<br>Sharing your feelings by talking is important.</p>
</section>

<section class="spread">
  <div class="panel panel-condition">
    <div class="photo-mother-baby" role="img" aria-label="Soft faded photo of a mother holding her newborn"></div>
    <svg class="band-top" width="267" height="110" viewBox="0 0 267 110" aria-hidden="true">
      <path d="M0 0H267V32C170 40 80 62 0 95Z" fill="#b5d96a"/>
      <path d="M0 0H267V22C170 30 80 52 0 84Z" fill="#3d7a1e"/>
    </svg>
    <h2 class="condition-title">DEPRESSION-<br>During and<br>After<br>Pregnancy</h2>
    <div class="condition-body">
      <p>Depression is more than just the “Baby Blues” (feeling weepy and irritable), or feeling “down in the dumps” for a few days. With depression, sad, anxious or empty feelings don’t go away.</p>
      <p>They interfere with your daily life and routines. The good news is that most people with depression get better with treatment.</p>
      <p>How do I know if I have depression?<br>If you have any of the following symptoms for more than two weeks:</p>
      <ul class="symptoms">
        <li>Feeling restless or moody</li>
        <li>Feeling sad, hopeless and overwhelmed</li>
        <li>Crying</li>
        <li>Having no energy or motivation</li>
        <li>Eating too much or too little</li>
        <li>Sleeping too much or too little</li>
        <li>Withdrawing from family or friends</li>
        <li>Having memory problems</li>
        <li>Feeling worthless or guilty</li>
        <li>Experiencing headaches, aches and pains</li>
        <li>Having trouble focusing or making decisions</li>
        <li>Losing interest in pleasurable activities you used to enjoy.</li>
      </ul>
    </div>
    <svg class="band-bottom" width="267" height="72" viewBox="0 0 267 72" aria-hidden="true">
      <path d="M0 14C90 30 180 22 267 0V72H0Z" fill="#b5d96a"/>
      <path d="M0 24C90 40 180 32 267 10V72H0Z" fill="#3d7a1e"/>
    </svg>
  </div>

  <div class="panel panel-impact">
    <div class="photo-sky" role="img" aria-label="Photo of a bright sky with soft clouds"></div>
    <svg class="band-top" width="267" height="30" viewBox="0 0 267 30" aria-hidden="true">
      <path d="M0 0H267V10C180 12 90 20 0 28Z" fill="#b5d96a"/>
      <path d="M0 0H267V4C180 6 90 12 0 20Z" fill="#3d7a1e"/>
    </svg>
    <div class="impact-body">
      <p>Depression impacts on the whole family, including baby.<br>You may feel guilty and a “not good enough mother”, you may lose confidence.</p>
      <p>Depression can be treated with counselling, “talk therapy”. A check up at your doctor is advisable too.</p>
      <p>Postpartum depression doesn't discriminate. It affects women of all ages, cultural and social standing.</p>
      <p>“Sometimes”, said Bramble “The smallest thing takes up the most room in your heart.”</p>
    </div>
    <div class="photo-consult" role="img" aria-label="Photo of a doctor listening to a worried young woman"></div>
    <svg class="band-bottom" width="267" height="72" viewBox="0 0 267 72" aria-hidden="true">
      <path d="M0 0C90 22 180 26 267 14V72H0Z" fill="#b5d96a"/>
      <path d="M0 10C90 32 180 36 267 24V72H0Z" fill="#3d7a1e"/>
    </svg>
  </div>

  <div class="panel panel-selfcare">
    <svg class="band-top" width="266" height="60" viewBox="0 0 266 60" aria-hidden="true">
      <path d="M0 0H266V50C180 34 90 24 0 22Z" fill="#b5d96a"/>
      <path d="M0 0H266V36C180 22 90 14 0 12Z" fill="#3d7a1e"/>
    </svg>
    <h2 class="selfcare-title">Looking after yourself</h2>
    <div class="selfcare-list">
      <h3>Rest</h3>
      <p>Sleep if you can, and have a rest if you can't. Nap when your baby is sleeping.</p>
      <h3>Diet</h3>
      <p>Eat a healthy, well-balanced diet. With all the new demands on your body, good nutrition is very important. Try not to skip meals.</p>
      <h3>Exercise</h3>
      <p>Although it may be the last thing you feel like doing; some gentle exercise will help you to feel better both physically and mentally. Just going for a walk with your baby can help.</p>
      <h3>Meditate</h3>
      <p>It may be difficult to quieten your mind; a guided meditation on CD may help.</p>
      <h3>Stay connected</h3>
      <p>Having a baby can make you feel isolated. Meet with other new mothers, join a supportive mothers group.</p>
      <h3>Be kind to yourself</h3>
      <p>You need to take care of yourself to take care of your baby. Don't load yourself up with things that really don't need to be done.<br>Know how little can be enough.</p>
      <h3>Help ..................ask and accept</h3>
      <p>Ask and accept offers of help around the home and with meals.<br>You may not need professional help at the moment, surround yourself with people you can be honest with, share how you are feeling.</p>
    </div>
    <svg class="band-bottom" width="266" height="72" viewBox="0 0 266 72" aria-hidden="true">
      <path d="M0 14C90 4 180 0 266 4V72H0Z" fill="#b5d96a"/>
      <path d="M0 24C90 14 180 10 266 14V72H0Z" fill="#3d7a1e"/>
    </svg>
  </div>
</section>

</body>
</html>
```